New Zealand Marlborough Sauvignon Blanc wine packaging design

We need packaging design for our new wine brand, Dunmore Vale. The wine is a New Zealand Marlborough Sauvignon Blanc. We would like the packaging will portray elegance and style with an understated label. We are looking for a label that portrays the elegance of the French Riviera. The label should be round or pill shaped.
Updates

Industry/Entity Type

Wine

Font styles to use
Serif
Sans Serif

Requirements
Must have
• The words in order of importance: Dunmore Vale, Sauvignon Blanc, Marlborough, New Zealand. It should be fit to the bottle posted in the links
Nice to have
• a pill shape or circular shape
Should not have
• Illustrations of wine bottles, wine glasses, or grapes

```html
<!DOCTYPE html>
<html lang="en">
<head>
<meta charset="utf-8">
<title>Dunmore Vale Sauvignon Blanc – Label</title>
<link rel="stylesheet" href="https://fonts.googleapis.com/css2?family=Playfair+Display:wght@400;500&display=swap">
<style>
  :root {
    --page: #ffffff;
    --lime: #d6df2a;
    --leaf: #9cc93a;
    --green: #6cbb5a;
    --sea-green: #7cc7a4;
    --sky: #4fb6d6;
    --sand: #e2e58a;
    --sand-dark: #b9b77a;
    --shore: #cfe6a8;
    --water: #8fd0e6;
    --ink: #ffffff;
  }
  * { margin: 0; padding: 0; box-sizing: border-box; }
  html, body {
    width: 1200px;
    height: 675px;
    overflow: hidden;
    background: var(--page);
  }
  .canvas {
    position: relative;
    width: 1200px;
    height: 675px;
    background: var(--page);
  }
  .label {
    position: absolute;
    left: 396px;
    top: 38px;
    width: 408px;
    height: 600px;
    border-radius: 50% / 36%;
    overflow: hidden;
  }
  .label-art {
    position: absolute;
    inset: 0;
    background:
      linear-gradient(180deg,
        transparent 0%, transparent 72%,
        var(--sand) 73%, var(--lime) 76%,
        var(--sand) 80%, var(--sand-dark) 83%,
        var(--sand-dark) 86%, var(--shore) 89%,
        var(--shore) 93%, var(--water) 96%, var(--water) 100%),
      radial-gradient(ellipse 60% 30% at 40% 14%, rgba(232,228,40,0.9), transparent 70%),
      linear-gradient(180deg,
        var(--lime) 0%, var(--leaf) 22%, var(--green) 40%,
        var(--sea-green) 56%, var(--sky) 70%, var(--sky) 100%);
  }
  .brand {
    position: absolute;
    left: 0;
    width: 100%;
    text-align: center;
    font-family: "Playfair Display", serif;
    font-weight: 400;
    color: var(--ink);
    line-height: 1;
    transform: scaleX(0.72);
  }
  .brand-first { top: 98px; font-size: 104px; letter-spacing: -2px; }
  .brand-second { top: 188px; font-size: 104px; letter-spacing: -2px; }
  .varietal {
    position: absolute;
    left: 0;
    top: 326px;
    width: 100%;
    text-align: center;
    font-family: "Playfair Display", serif;
    font-weight: 400;
    font-size: 46px;
    color: var(--ink);
    line-height: 1;
    transform: scaleX(0.7);
  }
  .region {
    position: absolute;
    left: 0;
    top: 478px;
    width: 100%;
    text-align: center;
    font-family: "Playfair Display", serif;
    font-weight: 500;
    font-size: 21px;
    color: var(--ink);
    line-height: 1;
    transform: scaleX(0.72);
  }
</style>
</head>
<body>
  <main class="canvas">
    <section class="label">
      <div class="label-art" role="img" aria-label="Watercolour wash from lime and green to sea blue, with a beach of sand bands, shoreline and two starfish"></div>
      <h1 class="brand brand-first">Dunmore</h1>
      <p class="brand brand-second">Vale</p>
      <h2 class="varietal">Sauvignon Blanc</h2>
      <p class="region">Marlborough, New Zealand</p>
    </section>
  </main>
</body>
</html>
```